Healthcare and Professional IT Services Company need a redesigned business card

We are a IT Services company that targets small medical practices and professional business such as Attorneys, Accounts, Architects etc. We want to communicate a professional yet friendly image using recent logo redesign here on ArtHarbor. Like to see the colors blue and orange in the design. Must use the Tall Pine Computing as displayed in the new logo - then also want to incorporate the fish logo as well.

Target Market(s)

Small medical and professional services

Industry/Entity Type

It Company

Contact Information for Business Card

The usual stuff, place for name address phone website. Also maybe our tagline which is "hooked on technology"

Requirements
Must have
• My new logo and the fish somewhere on the card

```html
<!DOCTYPE html>
<html lang="en">
<head>
<meta charset="utf-8">
<title>Tall Pine Computing — Business Card</title>
<link href="https://fonts.googleapis.com/css2?family=Open+Sans:wght@400;600&display=swap" rel="stylesheet">
<style>
  :root {
    --stage: #eceeef;
    --card: #ffffff;
    --blue: #3aa6dc;
    --blue-light: #5ab6e4;
    --logo-blue: #2f8fd0;
    --white: #ffffff;
    --shadow: rgba(0, 0, 0, 0.12);
  }
  * { margin: 0; padding: 0; box-sizing: border-box; }
  html, body {
    width: 1200px;
    height: 892px;
    overflow: hidden;
    background: var(--stage);
    font-family: "Open Sans", Arial, sans-serif;
  }
  .stage {
    position: relative;
    width: 1200px;
    height: 892px;
  }
  .card {
    position: absolute;
    left: 250px;
    width: 700px;
    height: 400px;
    background: var(--card);
    box-shadow: 0 4px 18px var(--shadow);
    overflow: hidden;
  }
  .card--front { top: 30px; }
  .card--back { top: 462px; }

  /* front face */
  .contact-panel {
    position: absolute;
    left: 0;
    top: 52px;
    width: 430px;
    height: 296px;
    background: linear-gradient(135deg, var(--blue) 0%, var(--blue-light) 100%);
    border-radius: 0 14px 14px 0;
    color: var(--white);
    text-align: right;
    padding: 34px 28px 0 0;
  }
  .contact-name {
    font-size: 34px;
    font-weight: 400;
    letter-spacing: 1px;
    margin-bottom: 44px;
  }
  .contact-list { list-style: none; }
  .contact-item {
    display: flex;
    justify-content: flex-end;
    align-items: center;
    gap: 12px;
    font-size: 17px;
    line-height: 1.25;
    margin-bottom: 6px;
  }
  .contact-icon {
    width: 18px;
    height: 18px;
    background: var(--white);
    border-radius: 2px;
    display: flex;
    align-items: center;
    justify-content: center;
    flex: none;
  }
  .contact-icon svg { width: 12px; height: 12px; }

  .front-logo {
    position: absolute;
    left: 448px;
    top: 170px;
    width: 190px;
    text-align: center;
    color: var(--logo-blue);
    font-weight: 600;
    font-size: 26px;
    line-height: 1.1;
  }
  .accent-strip {
    position: absolute;
    right: 0;
    top: 94px;
    width: 42px;
    height: 270px;
    background: var(--blue-light);
    border-radius: 12px 0 0 12px;
  }

  /* back face */
  .back-logo {
    position: absolute;
    inset: 0;
    display: flex;
    align-items: center;
    justify-content: center;
    gap: 18px;
  }
  .back-logo__dot {
    width: 44px;
    height: 44px;
    border-radius: 50%;
    background: var(--logo-blue);
  }
  .back-logo__name {
    color: var(--logo-blue);
    font-weight: 600;
    font-size: 50px;
  }
</style>
</head>
<body>
<main class="stage">

  <section class="card card--front" aria-label="Business card front">
    <div class="contact-panel">
      <h1 class="contact-name">Martin Kessler</h1>
      <ul class="contact-list">
        <li class="contact-item">+1 555 0142 7788
          <span class="contact-icon">
            <svg viewBox="0 0 12 12"><path d="M3 1 L5 3 L4 4.5 Q5 7 7.5 8 L9 7 L11 9 L9.5 11 Q2 10 1 2.5 Z" fill="var(--blue)"/></svg>
          </span>
        </li>
        <li class="contact-item">www.tallpinecomputing.com
          <span class="contact-icon">
            <svg viewBox="0 0 12 12"><circle cx="6" cy="6" r="4.5" fill="none" stroke="var(--blue)" stroke-width="1.3"/><line x1="1.5" y1="6" x2="10.5" y2="6" stroke="var(--blue)" stroke-width="1"/><ellipse cx="6" cy="6" rx="2" ry="4.5" fill="none" stroke="var(--blue)" stroke-width="1"/></svg>
          </span>
        </li>
        <li class="contact-item">4820 Cedar Row, Millbrook, BC
          <span class="contact-icon">
            <svg viewBox="0 0 12 12"><path d="M6 11 Q2 6 2 4.5 A4 4 0 0 1 10 4.5 Q10 6 6 11 Z" fill="var(--blue)"/><circle cx="6" cy="4.5" r="1.4" fill="var(--white)"/></svg>
          </span>
        </li>
      </ul>
    </div>
    <div class="front-logo">Tall Pine Computing</div>
    <div class="accent-strip"></div>
  </section>

  <section class="card card--back" aria-label="Business card back">
    <div class="back-logo">
      <span class="back-logo__dot"></span>
      <span class="back-logo__name">Tall Pine Computing</span>
    </div>
  </section>

</main>
</body>
</html>
```